Beacon Advisory Website

I currently have a website www.beaconadvisoryinc.com. We are a IT Consulting Company. Our website will pretty much tell out our services. I am looking to enhance my website and make it look more professional. Looking for very classy and Contemporary look and design for my website.

It Company

```html
<!DOCTYPE html>
<html lang="en">
<head>
<meta charset="utf-8">
<title>Beacon Advisory</title>
<link href="https://fonts.googleapis.com/css2?family=Lato:wght@400;700;900&display=swap" rel="stylesheet">
<style>
:root{
  --sky:#039bd9;
  --navy:#0b3a86;
  --navy-deep:#082f6d;
  --ink:#333333;
  --charcoal:#353535;
  --nav:#3a3a3a;
  --text:#3c3c3c;
  --line:#d7d7d7;
  --white:#ffffff;
}
*{box-sizing:border-box;margin:0;padding:0}
html,body{width:1147px;height:1200px;overflow:hidden}
body{font-family:'Lato',sans-serif;background:var(--white);color:var(--text);position:relative}
.topbar{height:33px;background:var(--sky);position:relative}
.social-top{position:absolute;right:94px;top:0;display:flex}
.social-top span{width:35px;height:33px;background:var(--navy);border-left:1px solid #2b5aa0}
.header{height:82px;position:relative}
.brand{position:absolute;left:94px;top:24px;display:flex;align-items:center;gap:10px}
.brand-mark{width:30px;height:30px;background:var(--navy);border-radius:3px}
.brand-name{font-weight:900;font-size:20px;color:var(--navy);letter-spacing:.5px}
.phone{position:absolute;right:94px;top:30px;display:flex;align-items:center;gap:7px;font-size:17px;font-weight:700;color:var(--ink)}
.nav{height:41px;background:var(--nav);display:flex;padding-left:94px}
.nav a{color:var(--white);text-decoration:none;font-size:15px;font-weight:700;display:flex;align-items:center;justify-content:center;border-right:1px solid #2c2c2c;position:relative}
.nav a.active{background:var(--sky)}
.nav a.active::after{content:"";position:absolute;bottom:0;left:50%;margin-left:-6px;border:6px solid transparent;border-bottom-color:var(--white)}
.hero{height:276px;background:radial-gradient(ellipse at 20% 45%,#c9b7a8 0,#7d8fa0 18%,transparent 35%),linear-gradient(100deg,#5b7a98 0%,#3d6a93 35%,#6ea0c4 60%,#2f6590 100%)}
.welcome{height:174px;background:linear-gradient(90deg,rgba(11,58,134,.95),rgba(13,70,150,.92) 50%,rgba(11,58,134,.95));text-align:center;color:var(--white);position:relative}
.welcome h1{font-size:29px;font-weight:900;padding-top:19px;letter-spacing:.2px}
.rule{width:660px;height:1px;background:rgba(255,255,255,.5);margin:12px auto 0;position:relative}
.rule::after{content:"";position:absolute;left:50%;top:0;margin-left:-9px;border:9px solid transparent;border-top-color:var(--white);border-bottom:0}
.welcome p{font-size:12.2px;font-weight:700;line-height:18.5px;width:940px;margin:18px auto 0}
.more{position:absolute;left:50%;bottom:0;width:36px;height:20px;margin-left:-18px;background:var(--white);border-radius:3px 3px 0 0;color:#888;font-size:20px;line-height:22px}
.cards{position:absolute;top:650px;left:94px;width:959px;display:flex;justify-content:space-between}
.card{width:295px;height:351px;border:1px solid #e2e2e2;border-top:3px solid var(--navy);position:relative;padding:16px 13px 0;box-shadow:0 12px 14px -10px rgba(0,0,0,.18)}
.card-title{display:flex;align-items:center;gap:13px;font-size:26px;font-weight:700;color:var(--ink);margin-bottom:15px;height:37px}
.card-title b{color:var(--navy);font-weight:700}
.card-icon{width:37px;height:37px;border-radius:50%;background:var(--charcoal);flex:none;display:flex;align-items:center;justify-content:center}
.card-img{height:117px;border:1px solid #ccc;margin-bottom:14px}
.img-office{background:linear-gradient(90deg,#7a8fa8 0%,#dfe6ee 45%,#eef2f5 100%)}
.img-globe{background:radial-gradient(ellipse at 60% 55%,#56a6d8 0,#1d6fae 45%,#0f4e86 100%)}
.card p{font-size:11.6px;line-height:16.8px;letter-spacing:0}
.services{list-style:none;margin-top:6px;width:205px}
.services li{display:flex;align-items:center;gap:10px;font-size:13px;color:var(--ink);height:32px;border-bottom:1px dotted #aaa}
.services li:last-child{border-bottom:0}
.services i{width:16px;height:16px;border:2px solid var(--navy);border-radius:50%;flex:none}
.plus{position:absolute;right:-1px;bottom:-1px;width:25px;height:24px;background:var(--navy);color:var(--white);font-size:22px;font-weight:700;text-align:center;line-height:23px}
.footer{position:absolute;top:1057px;left:0;width:1147px;height:143px;background:var(--charcoal);border-top:2px solid #222;color:var(--white)}
.footer-nav{position:absolute;left:96px;top:40px;font-size:13.5px;word-spacing:2px}
.footer-nav span{margin:0 5px;color:#bbb}
.newsletter{position:absolute;left:94px;top:81px;display:flex;align-items:center}
.mail{width:38px;height:38px;border-radius:50%;border:3px solid var(--white);background:var(--charcoal);z-index:1;display:flex;align-items:center;justify-content:center}
.field{width:175px;height:37px;background:var(--white);margin-left:-8px;border-radius:0 4px 4px 0;font-size:12px;color:#777;padding:12px 0 0 20px}
.subscribe{margin-left:9px;height:37px;width:98px;background:var(--navy);border-radius:3px;font-weight:700;font-size:14px;display:flex;align-items:center;justify-content:center}
.social-foot{display:flex;gap:8px;margin-left:24px}
.social-foot span{width:26px;height:26px;border-radius:50%;background:var(--white)}
.foot-brand{position:absolute;right:138px;top:40px;display:flex;align-items:center;gap:8px}
.foot-brand .brand-mark{background:#8a8a8a}
.foot-brand .brand-name{color:#a0a0a0}
.copyright{position:absolute;right:98px;top:108px;font-size:12.5px}
</style>
</head>
<body>
<div class="topbar"><div class="social-top"><span></span><span></span><span></span><span></span></div></div>
<header class="header">
  <div class="brand"><span class="brand-mark"></span><span class="brand-name">BEACON ADVISORY</span></div>
  <div class="phone">
    <svg width="24" height="24" viewBox="0 0 24 24"><circle cx="12" cy="12" r="10.5" fill="none" stroke="#0b3a86" stroke-width="2"/><path d="M8.5 6.5c-1 .6-1.4 1.8-.9 3.2 1 2.6 3 4.8 5.6 6 1.3.6 2.6.3 3.3-.7l-2-2-1.3.8c-1.2-.6-2.3-1.7-2.9-2.9l.8-1.3z" fill="#0b3a86"/></svg>
    123 555 0190
  </div>
</header>
<nav class="nav">
  <a class="active" style="width:166px">COMPANY</a>
  <a style="width:157px">SERVICES</a>
  <a style="width:174px">SOLUTIONS</a>
  <a style="width:175px">RESOURCES</a>
  <a style="width:147px">CAREER</a>
  <a style="width:140px;border-right:0">CONTACT US</a>
</nav>
<div class="hero" role="img" aria-label="Businessman touching a glowing world map interface"></div>
<section class="welcome">
  <h1>WELCOME TO BEACON ADVISORY</h1>
  <div class="rule"></div>
  <p>Today's IT market is a dynamic, fast-paced industry, with ever-increasing demands. Meeting these demands for over 25 years, Beacon Advisory maintains a global presence, aggressively recruiting expertly qualified IT and Management Professionals from around the world and cultivating key partnerships with corporations to understand their business models end-to-end, with a goal of delivering exceptional client service and ensuring a consistent delivery of the talent needed to drive results.</p>
  <div class="more">+</div>
</section>
<main class="cards">
  <article class="card">
    <h2 class="card-title"><span class="card-icon"><svg width="18" height="18" viewBox="0 0 18 18"><circle cx="9" cy="9" r="4" fill="#fff"/><g stroke="#fff" stroke-width="1.5"><path d="M9 0v3M9 15v3M0 9h3M15 9h3M2.6 2.6l2 2M13.4 13.4l2 2M2.6 15.4l2-2M13.4 4.6l2-2"/></g></svg></span><span><b>IT</b> CONSULTING</span></h2>
    <div class="card-img img-office" role="img" aria-label="Woman working on a laptop in a bright office"></div>
    <p>Information technology should improve business results. Northwind helps companies make sure it does. We look at IT issues strategically, in the broader context of our clients' business. Our experts provide an objective, independent perspective to help companies realize the full potential of their IT resources, investments and assets.</p>
    <div class="plus">+</div>
  </article>
  <article class="card">
    <h2 class="card-title"><span class="card-icon"><svg width="16" height="18" viewBox="0 0 16 18"><rect x="2" y="2" width="11" height="14" rx="1" fill="none" stroke="#fff" stroke-width="1.6"/><path d="M5 6h5M5 9h5M5 12h3" stroke="#fff" stroke-width="1.4"/></svg></span><span><b>WHAT</b> WE DO</span></h2>
    <p>We are successful in deploying all students we trained into project with 2-3 weeks after training program. Our training programs will last for 6-8 weeks dependents on technology. We will provide on job support for trainees until technology comfort level is attained.</p>
    <ul class="services">
      <li><i></i>Technology</li>
      <li><i></i>Offshore Business</li>
      <li><i></i>Application Developement</li>
      <li><i></i>Enterprise Integration</li>
      <li><i></i>IT Consulting</li>
    </ul>
    <div class="plus">+</div>
  </article>
  <article class="card">
    <h2 class="card-title"><span class="card-icon"><svg width="18" height="18" viewBox="0 0 18 18"><circle cx="9" cy="9" r="5" fill="none" stroke="#fff" stroke-width="2.4" stroke-dasharray="2.5 1.5"/><circle cx="9" cy="9" r="2" fill="#fff"/></svg></span><span><b>OFF</b>SHORE</span></h2>
    <div class="card-img img-globe" role="img" aria-label="Blue globe with glowing network connections"></div>
    <p>Our Offshore development model has a unique distinction of providing efficient software solutions with cost and quality advantage, using state-of-the-art technologies, having the capacity to handle large projects and, above all, the ability to execute timely deliveries.</p>
    <div class="plus">+</div>
  </article>
</main>
<footer class="footer">
  <div class="footer-nav">COMPANY<span>/</span>SERVICES<span>/</span>SOLUTIONS<span>/</span>RESOURCES<span>/</span>CAREER<span>/</span>CONTACT US</div>
  <div class="newsletter">
    <span class="mail"><svg width="18" height="13" viewBox="0 0 18 13"><rect x="1" y="1" width="16" height="11" fill="none" stroke="#fff" stroke-width="1.6"/><path d="M1 1l8 6 8-6" fill="none" stroke="#fff" stroke-width="1.6"/></svg></span>
    <div class="field">Sign Up for Newsletter</div>
    <div class="subscribe">SUBSCRIBE</div>
    <div class="social-foot"><span></span><span></span><span></span><span></span></div>
  </div>
  <div class="foot-brand"><span class="brand-mark"></span><span class="brand-name">BEACON ADVISORY</span></div>
  <div class="copyright">© 2016 BeaconAdvisory. All Right Reserved.</div>
</footer>
</body>
</html>
```